KTWG application splash screen

We need a 1024x768 image for use as an application splash screen.
The image will be displayed full screen on an 10 inch industrial PC 1024x768 screen while our application is launching. The image should convey that the application is "Waiting for connection to Wi-Fi access point..." and include a graphic of the industrial PC connected to the access point via an Ethernet cable. A list of troubleshooting steps should be included at the bottom of the image. The troubleshooting steps should not be the main focus of the image and should be shown in a smaller font (but still readable at 1024x768 displayed on a 10 inch screen).
I will include a mock up of the general idea of what we are looking for as well as image files for the industrial PC, a screenshot of our application to show on the PC's screen and the AP.
For general look and feel and a sense of corporate branding please review our website https://marrowgatesoilworks.example/. The splash screen should reflect corporate branding.
Target Market(s)
Users of our application
Industry/Entity Type
Agriculture
Look and feel

```html
<!DOCTYPE html>
<html lang="en">
<head>
<meta charset="utf-8">
<title>KTWG application splash screen</title>
<link rel="stylesheet" href="https://fonts.googleapis.com/css2?family=Figtree:wght@400;500;600&display=swap">
<style>
  :root {
    --page: #ffffff;
    --sheet: #f9f9f9;
    --green-deep: #1a8a5c;
    --green-mid: #2ea46f;
    --green-light: #55bd87;
    --green-pale: #79c7a2;
    --brand: #25a566;
    --ink: #2c2c2c;
    --white: #ffffff;
    --device-dark: #1c1c1c;
    --device-screen: #e8e8ea;
    --ap-white: #f1f3f2;
  }
  * { margin: 0; padding: 0; box-sizing: border-box; }
  html, body {
    width: 1200px; height: 1200px; overflow: hidden;
    background: var(--page);
    font-family: "Figtree", Arial, sans-serif;
  }
  .splash {
    position: absolute; left: 0; top: 150px;
    width: 1200px; height: 900px;
    background: var(--sheet);
    overflow: hidden;
  }
  .hero {
    position: absolute; left: 0; top: 0;
    width: 1200px; height: 713px;
    border-radius: 30px 30px 64px 64px;
    background:
      radial-gradient(ellipse 520px 420px at 560px 260px, rgba(85,189,135,0.55), transparent 70%),
      radial-gradient(ellipse 420px 360px at 1200px 0px, rgba(121,199,162,0.75), transparent 70%),
      linear-gradient(160deg, var(--green-mid) 0%, var(--green-deep) 55%, var(--green-mid) 100%);
    overflow: hidden;
  }
  .headline {
    position: absolute; left: 0; top: 250px; width: 1200px;
    text-align: center;
    color: var(--white);
    font-size: 37px; font-weight: 600; letter-spacing: -0.2px;
  }
  .device {
    position: absolute; left: 274px; top: 368px;
    width: 183px; height: 135px;
    border-radius: 8px;
    background: linear-gradient(180deg, var(--device-dark), #2a2a2a);
    box-shadow: 0 4px 10px rgba(0,0,0,0.25);
  }
  .device-screen {
    position: absolute; left: 8px; top: 8px; right: 8px; bottom: 20px;
    border-radius: 3px;
    background: linear-gradient(180deg, var(--device-screen), #d3e9dc);
  }
  .access-point {
    position: absolute; left: 875px; top: 350px;
    width: 22px; height: 158px;
    border-radius: 6px;
    background: linear-gradient(90deg, #dfe3e1, var(--ap-white), #d8dcda);
  }
  .cable { position: absolute; left: 0; top: 0; }
  .help { position: absolute; left: 52px; top: 744px; color: var(--ink); }
  .help-tag {
    display: inline-block;
    background: var(--brand); color: var(--white);
    font-size: 11.5px; font-weight: 500;
    padding: 4px 11px; border-radius: 12px;
  }
  .help-steps { list-style: none; margin-top: 9px; }
  .help-step { font-size: 11.5px; line-height: 21px; display: flex; align-items: center; gap: 4px; }
  .step-num {
    width: 11px; height: 11px; border-radius: 50%;
    border: 1px solid var(--brand); color: var(--brand);
    font-size: 8px; display: inline-flex; align-items: center; justify-content: center;
  }
  .help-actions { list-style: disc; margin-left: 28px; margin-top: -1px; }
  .help-actions li { font-size: 9.6px; line-height: 13px; }
  .brand-mark {
    position: absolute; left: 1010px; top: 798px;
    display: flex; align-items: center; gap: 7px;
    color: var(--brand); font-size: 30px; font-weight: 600;
  }
  .brand-square { width: 18px; height: 18px; background: var(--brand); border-radius: 3px; }
</style>
</head>
<body>
  <main class="splash">
    <section class="hero">
      <h1 class="headline">Waiting for connection to Wi-Fi access point...</h1>

      <div class="device" role="img" aria-label="Industrial panel PC showing the application's bar chart dashboard">
        <div class="device-screen"></div>
      </div>

      <svg class="cable" width="1200" height="713" viewBox="0 0 1200 713" aria-hidden="true">
        <path d="M437 503 V518 Q437 526 445 526 H738 Q746 526 746 518 V505 Q746 497 754 497 H876"
              fill="none" stroke="#ffffff" stroke-width="2" stroke-dasharray="6 4"/>
      </svg>

      <div class="access-point" role="img" aria-label="Outdoor Wi-Fi access point with two antennas"></div>
    </section>

    <section class="help">
      <span class="help-tag">Troubleshooting steps:</span>
      <ol class="help-steps">
        <li class="help-step"><span class="step-num">1</span>This screen should only be visible for a short time on boot.</li>
        <li class="help-step"><span class="step-num">2</span>If this screen stays visible for more than a minute:</li>
      </ol>
      <ul class="help-actions">
        <li>Verify that the Wi-Fi Access Point (AP) powers up when this system does (indicated by a green light on the side of the AP).</li>
        <li>Check the Ethernet cable between this system and the AP for damage, and replace it if necessary.</li>
        <li>Power-cycle this system and wait for it to reboot fully.</li>
        <li>If the issue persists, contact KTWG support for further assistance.</li>
      </ul>
    </section>

    <div class="brand-mark"><span class="brand-square"></span>KTWG</div>
  </main>
</body>
</html>
```